Halvery Construction Group Website

Need a dynamic corporate website that can be built on with time. We want to get our information out to the world and have a place where customers can submit requests for proposals.

Target Market(s)

Custom home owners and buyers. Architects and Real Estate Agents.

Industry/Entity Type

Construction

Number of Pages Required

3 page

Font styles to use
Serif
Sans Serif

Requirements
Must have
• Company logo, about, company contact information, biography, contact, projects,
• Sleek, modern, clean, attractive design.
• Online form customers can use for filling out a request for project proposal.
• Linkedin hyperlink.
• Uses www.halveryconstructiongroup.example

```html
<!DOCTYPE html>
<html lang="en">
<head>
<meta charset="utf-8">
<title>Halvery Construction Group</title>
<link href="https://fonts.googleapis.com/css2?family=Montserrat:wght@300;400;600;700&family=Open+Sans:wght@400;600&display=swap" rel="stylesheet">
<style>
:root{
  --navy:#141d5c;
  --navy-deep:#0d1446;
  --blue:#2a3bb0;
  --blue-bright:#3d6cf0;
  --sky:#8fb6e6;
  --ink:#222;
  --muted:#666;
  --grey-band:#8a8a8a;
  --white:#fff;
}
*{box-sizing:border-box;margin:0;padding:0}
html,body{width:1200px;height:3428px;overflow:hidden}
body{font-family:"Open Sans",Arial,sans-serif;color:var(--ink);background:var(--white);position:relative}
section,header,footer,.topbar{position:absolute;left:0;width:1200px}
h2{font-family:"Montserrat",Arial,sans-serif;font-weight:400;text-transform:uppercase;text-align:center;letter-spacing:1px}
.sub{font-family:"Montserrat",Arial,sans-serif;text-transform:uppercase;text-align:center;font-size:17px;letter-spacing:1px}

.topbar{top:0;height:40px;background:var(--navy-deep);color:#c9d3ff;font-size:13px;display:flex;justify-content:space-between;align-items:center;padding:0 80px}
.topbar nav a{color:#fff;margin-left:34px;text-decoration:none}

.site-header{top:40px;height:110px;background:var(--white);display:flex;align-items:center;justify-content:space-between;padding:0 80px}
.brand{display:flex;align-items:center;gap:14px;font-family:"Montserrat",Arial,sans-serif;font-weight:700;font-size:22px;color:var(--navy);text-transform:uppercase}
.brand-box{width:44px;height:44px;background:var(--blue)}
.main-nav a{font-family:"Montserrat",Arial,sans-serif;font-size:15px;color:#333;text-decoration:none;margin-left:42px;text-transform:uppercase}
.main-nav a.active{color:var(--navy);font-weight:600}

.hero{top:150px;height:560px}
.hero-photo{position:absolute;inset:0;background:linear-gradient(180deg,#5b86c4 0%,#8fb0dc 55%,#a9c2e2 100%)}
.hero h1{position:absolute;top:110px;width:100%;text-align:center;font-family:"Montserrat",Arial,sans-serif;font-weight:400;font-size:84px;line-height:96px;color:var(--white);text-transform:uppercase;letter-spacing:2px}
.hero svg{position:absolute;bottom:0;left:0}

.welcome{top:710px;height:300px;text-align:center}
.welcome h2{font-size:42px;color:#333;margin-top:10px}
.welcome h2 span{color:var(--blue-bright)}
.welcome .sub{color:#555;font-size:16px;margin-top:2px}
.welcome p{width:960px;margin:28px auto 0;font-size:13px;line-height:20px;color:var(--muted);text-align:left}
.btn{display:inline-flex;align-items:center;gap:10px;background:var(--navy);color:#fff;font-family:"Montserrat",Arial,sans-serif;font-size:14px;font-weight:600;border-radius:24px;padding:0 8px 0 26px;height:48px;text-transform:uppercase}
.btn i{width:34px;height:34px;border-radius:50%;background:var(--white);display:block}
.welcome .btn{margin-top:30px}

.workflow{top:990px;height:600px;color:#fff}
.workflow-bg{position:absolute;inset:0;background:linear-gradient(180deg,#3340b8 0%,#2430a0 55%,#161f78 100%)}
.workflow svg.shape{position:absolute;left:0;top:0}
.workflow h2{position:absolute;top:80px;width:100%;font-size:44px}
.workflow .sub{position:absolute;top:134px;width:100%}
.step{position:absolute;font-family:"Montserrat",Arial,sans-serif;font-size:30px;text-align:center;line-height:36px}
.center-name{position:absolute;top:420px;width:100%;text-align:center;font-family:"Montserrat",Arial,sans-serif;font-weight:700;font-size:46px;letter-spacing:3px;text-transform:uppercase}

.projects{top:1590px;height:560px}
.projects h2{font-size:42px;color:#333;margin-top:40px}
.projects .sub{color:#555;font-size:16px}
.tabs{display:flex;justify-content:center;gap:40px;margin-top:30px;font-size:13px;color:#555}
.tabs span.active{border-bottom:2px solid var(--navy);padding-bottom:4px;color:#222;font-weight:600}
.grid{position:absolute;left:80px;top:190px;display:grid;grid-template-columns:repeat(4,248px);gap:16px 16px}
.card{position:relative;height:160px}
.card .photo{position:absolute;inset:0}
.card .label{position:absolute;left:0;right:0;top:55px;height:46px;background:rgba(10,16,60,.55);color:#fff;font-size:18px;display:flex;align-items:center;padding-left:40px}

.testimonial{top:2150px;height:480px;color:#fff}
.testimonial svg{position:absolute;top:0;left:0}
.testimonial h2{position:absolute;top:110px;width:100%;font-size:44px}
.testimonial .sub{position:absolute;top:162px;width:100%}
.quote{position:absolute;top:230px;width:520px;display:flex;gap:24px}
.avatar-col{width:160px;flex:none;text-align:center}
.avatar{width:120px;height:120px;border-radius:50%;border:5px solid #fff;margin:0 auto}
.avatar-col b{display:block;font-size:14px;font-weight:600;margin-top:18px;text-transform:uppercase;white-space:nowrap}
.quote p{font-size:15px;line-height:22px;position:relative;padding-left:30px}
.quote p::before{content:"\201C";position:absolute;left:0;top:-18px;font-family:Georgia,serif;font-size:60px}

.inquiry{top:2630px;height:460px;color:#fff}
.inquiry-bg{position:absolute;inset:0;background:linear-gradient(180deg,#1a2380 0%,#223399 60%,#2b3fb0 100%)}
.inquiry h2{position:absolute;top:40px;width:100%;font-size:44px}
.inquiry .sub{position:absolute;top:94px;width:100%}
.form{position:absolute;left:80px;top:140px;width:1040px}
.row{display:grid;grid-template-columns:repeat(4,1fr);gap:16px}
.field{height:40px;background:#1a2264;border:1px solid #3a47b0;font-size:13px;padding:10px 14px;color:#cfd6ff}
.field.message{height:140px;margin-top:12px}
.inquiry .btn{position:absolute;left:505px;top:360px;background:#fff;color:var(--navy)}
.inquiry .btn i{background:var(--navy)}

.site-footer{top:3090px;height:310px;background:#1b2a6e;color:#fff}
.footer-wave{position:absolute;left:0;top:0}
.col{position:absolute;top:90px;font-size:13px;line-height:24px}
.col h3{font-family:"Montserrat",Arial,sans-serif;font-size:16px;font-weight:600;margin-bottom:10px}
.contact-line{display:flex;gap:10px;align-items:flex-start}
.map{position:absolute;left:590px;top:90px;width:230px;height:170px;background:linear-gradient(135deg,#e8ecef,#cfd8cf)}
.foot-name{position:absolute;left:880px;top:90px;width:240px;height:170px;border:2px solid #fff;display:flex;align-items:center;justify-content:center;font-family:"Montserrat",Arial,sans-serif;font-weight:700;font-size:26px;letter-spacing:2px}
.bottombar{position:absolute;left:0;top:3400px;width:1200px;height:28px;background:#111a4a;color:#c9d3ff;font-size:11px;display:flex;justify-content:space-between;align-items:center;padding:0 80px}
.social{display:flex;gap:8px}
.social i{width:18px;height:18px;border-radius:50%;background:var(--blue-bright);display:block}
</style>
</head>
<body>

<div class="topbar">
  <span>Great News! Welcome to Halvery Construction Group, Inc.</span>
  <nav><a href="#">Extras</a><a href="#">Support</a><a href="#">Clients</a><a href="#">Investors</a></nav>
</div>

<header class="site-header">
  <div class="brand"><span class="brand-box"></span>Halvery Construction Group</div>
  <nav class="main-nav"><a class="active" href="#">Home</a><a href="#">About</a><a href="#">Projects</a><a href="#">Contact</a></nav>
</header>

<section class="hero">
  <div class="hero-photo" role="img" aria-label="Hero photograph of a coastal city skyline by the sea"></div>
  <h1>We put sparkle<br>in your work</h1>
  <svg width="1200" height="80" viewBox="0 0 1200 80"><path d="M0 40 Q600 90 1200 40 L1200 80 L0 80Z" fill="#fff"/></svg>
</section>

<section class="welcome">
  <h2>Welcome to <span>Halvery</span></h2>
  <div class="sub">Construction Group, Inc.</div>
  <p>Lorem Ipsum is simply dummy text of the printing and typesetting industry. Lorem Ipsum has been the industry's standard dummy text ever since the 1500s, when an unknown printer took a galley of type and scrambled it to make a type specimen book. It has survived not only five centuries, but also the leap into electronic typesetting, remaining essentially unchanged.</p>
  <span class="btn">Read more <i></i></span>
</section>

<section class="workflow">
  <div class="workflow-bg"></div>
  <svg class="shape" width="1200" height="600" viewBox="0 0 1200 600">
    <path d="M0 0 L1200 0 L1200 30 Q600 -10 0 30Z" fill="#fff"/>
    <path d="M280 360 Q300 260 560 235" stroke="#fff" stroke-width="3" fill="none"/>
    <path d="M920 360 Q900 260 640 235" stroke="#fff" stroke-width="3" fill="none"/>
    <circle cx="600" cy="230" r="36" fill="#fff"/>
    <circle cx="280" cy="370" r="32" fill="#fff"/>
    <circle cx="920" cy="370" r="32" fill="#fff"/>
    <circle cx="252" cy="340" r="13" fill="var(--blue-bright)"/>
    <circle cx="892" cy="340" r="13" fill="var(--blue-bright)"/>
    <text x="252" y="345" font-size="13" fill="#fff" text-anchor="middle" font-family="Montserrat, sans-serif">1</text>
    <text x="892" y="345" font-size="13" fill="#fff" text-anchor="middle" font-family="Montserrat, sans-serif">3</text>
    <rect x="585" y="216" width="30" height="26" fill="none" stroke="var(--navy)" stroke-width="3"/>
    <path d="M266 362 h28 M266 372 h28 M266 382 h20" stroke="var(--navy)" stroke-width="3"/>
    <path d="M906 384 v-16 l14-12 14 12 v16z" fill="none" stroke="var(--navy)" stroke-width="3"/>
  </svg>
  <h2>How we work</h2>
  <div class="sub">Our workflow</div>
  <div class="step" style="left:660px;top:212px">Design &amp; Build</div>
  <div class="step" style="left:160px;top:420px;width:240px">Get The<br>Requirement</div>
  <div class="step" style="left:800px;top:420px;width:240px">Handover<br>Construction</div>
  <div class="center-name">Halvery</div>
</section>

<section class="projects">
  <h2>Projects</h2>
  <div class="sub">Check out our work</div>
  <div class="tabs"><span class="active">ALL PROJECTS</span><span>Buildings</span><span>Residency</span><span>Interior</span><span>Exterior</span></div>
  <div class="grid">
    <div class="card"><div class="photo" role="img" aria-label="Modern house exterior at dusk" style="background:linear-gradient(160deg,#5a6f8a,#2b3342)"></div><div class="label">Project Name</div></div>
    <div class="card"><div class="photo" role="img" aria-label="Contemporary home with lit windows" style="background:linear-gradient(160deg,#3a3f4a,#1c2026)"></div><div class="label">Project Name</div></div>
    <div class="card"><div class="photo" role="img" aria-label="Residence with lawn and trees" style="background:linear-gradient(160deg,#7f95b0,#485a45)"></div><div class="label">Project Name</div></div>
    <div class="card"><div class="photo" role="img" aria-label="Stone facade family home" style="background:linear-gradient(160deg,#8a7a68,#4a3e33)"></div><div class="label">Project Name</div></div>
    <div class="card"><div class="photo" role="img" aria-label="Villa with pool in the evening" style="background:linear-gradient(160deg,#4f6c8f,#1f3a52)"></div><div class="label">Project Name</div></div>
    <div class="card"><div class="photo" role="img" aria-label="Glass fronted house at night" style="background:linear-gradient(160deg,#2e3a55,#161b28)"></div><div class="label">Project Name</div></div>
    <div class="card"><div class="photo" role="img" aria-label="White modern villa with terrace" style="background:linear-gradient(160deg,#c7ced6,#6d7a86)"></div><div class="label">Project Name</div></div>
    <div class="card"><div class="photo" role="img" aria-label="Multi storey residential building" style="background:linear-gradient(160deg,#b7a58c,#5e4f3e)"></div><div class="label">Project Name</div></div>
  </div>
</section>

<section class="testimonial">
  <svg width="1200" height="480" viewBox="0 0 1200 480"><path d="M0 70 Q600 0 1200 70 L1200 480 L0 480Z" fill="var(--grey-band)"/></svg>
  <h2>Testimonial</h2>
  <div class="sub">What clients say about us</div>
  <div class="quote" style="left:60px">
    <div class="avatar-col"><div class="avatar" role="img" aria-label="Portrait of client Maren Tolliver" style="background:#e0c9a8"></div><b>Maren Tolliver</b></div>
    <p>Lorem Ipsum is simply dummy text of the printing and typesetting industry. Lorem Ipsum has been the industry's standard dummy text ever since the 1500s, when an unknown printer took a galley of type and scrambled it to make a type specimen book.</p>
  </div>
  <div class="quote" style="left:610px">
    <div class="avatar-col"><div class="avatar" role="img" aria-label="Portrait of client Caleb Ostrand" style="background:#c9b39a"></div><b>Caleb Ostrand</b></div>
    <p>Lorem Ipsum is simply dummy text of the printing and typesetting industry. Lorem Ipsum has been the industry's standard dummy text ever since the 1500s, when an unknown printer took a galley of type and scrambled it to make a type specimen book.</p>
  </div>
</section>

<section class="inquiry">
  <div class="inquiry-bg"></div>
  <h2>Quick inquiry</h2>
  <div class="sub">Request an estimate</div>
  <div class="form">
    <div class="row"><div class="field">Name</div><div class="field">E-Mail</div><div class="field">Phone</div><div class="field">Services</div></div>
    <div class="field message">Message</div>
  </div>
  <span class="btn">Submit <i></i></span>
</section>

<footer class="site-footer">
  <svg class="footer-wave" width="1200" height="60" viewBox="0 0 1200 60"><path d="M0 0 L1200 0 L1200 20 Q600 60 0 20Z" fill="#2b3fb0"/></svg>
  <div class="col" style="left:80px"><h3>Quick Links</h3>Home<br>About<br>Projects<br>Contact</div>
  <div class="col" style="left:340px">
    <h3>Contact Info</h3>
    <div class="contact-line"><svg width="14" height="18" viewBox="0 0 14 18"><path d="M7 0a7 7 0 0 1 7 7c0 5-7 11-7 11S0 12 0 7a7 7 0 0 1 7-7z" fill="#fff"/></svg><span>PO Box 1234, Street Name<br>City Name, Country<br>123456</span></div>
    <div class="contact-line"><svg width="14" height="14" viewBox="0 0 14 14"><path d="M3 0l3 3-2 2a8 8 0 0 0 5 5l2-2 3 3-2 3C6 14 0 8 0 3z" fill="#fff"/></svg><span>555 0143 872</span></div>
    <div class="contact-line"><svg width="14" height="12" viewBox="0 0 14 12"><rect width="14" height="12" fill="#fff"/><path d="M0 0l7 6 7-6" stroke="#1b2a6e" fill="none"/></svg><span>info@halverygroup.example</span></div>
  </div>
  <div class="map" role="img" aria-label="Street map showing the office location"></div>
  <div class="foot-name">HALVERY</div>
</footer>
<div class="bottombar"><span>© Halvery Construction Group · www.halveryconstructiongroup.example · All Rights Reserved</span><div class="social"><i></i><i></i><i></i><i></i><i></i></div></div>

</body>
</html>
```